Verdant Systems Business Card

want the back of card to be blue- with the logo in the center
front of card- info plus logo (info being mailing address, email address, and website address )
4 different names with titles to have on cards
1) Calvin Borsted - Owner
2) Naomi Trelvik- Customer Relationship Specialist
3) Felix Andrade- Vice President of Sales
4) Owen Markby- Chief Technology Officer

Target Market(s)

tech company in the government/probation office industry

Industry/Entity Type

Government Office

Contact Information for Business Card

1) Calvin Borsted - Owner

Colors
0355a3
ffffff

Requirements
Must have
• back side should be blue, with the logo placed in the center
• front side needs to include both the logo, as well as company info (info should include website address, email address, and mailing address)

```html
<!DOCTYPE html>
<html lang="en">
<head>
<meta charset="utf-8">
<title>Verdant Systems Business Card</title>
<link href="https://fonts.googleapis.com/css2?family=Crimson+Text:wght@600&family=Roboto:wght@400&display=swap" rel="stylesheet">
<style>
  :root {
    --brand-blue: #0355a3;
    --grey: #8c8c8c;
    --white: #ffffff;
    --page: #ecebe8;
  }
  * { margin: 0; padding: 0; box-sizing: border-box; }
  html, body {
    width: 1125px; height: 1200px; overflow: hidden;
    background: var(--page);
  }
  .card {
    position: absolute;
    left: 162px;
    width: 800px;
    height: 457px;
    overflow: hidden;
    box-shadow: 0 3px 8px rgba(0,0,0,0.25);
  }
  .card-front { top: 110px; background: var(--white); }
  .card-back { top: 630px; background: var(--brand-blue); }

  .front-wave { position: absolute; inset: 0; width: 800px; height: 457px; }

  .brand {
    position: absolute;
    display: flex; align-items: center; gap: 14px;
    font-family: "Crimson Text", serif;
    font-weight: 600;
    white-space: nowrap;
  }
  .brand-mark { display: block; }
  .front-brand { left: 58px; top: 110px; font-size: 44px; color: var(--brand-blue); }
  .front-brand .brand-mark { width: 22px; height: 22px; background: var(--brand-blue); }

  .contact-block {
    position: absolute; right: 32px; top: 236px;
    text-align: right; color: var(--white);
  }
  .person-name {
    font-family: "Crimson Text", serif; font-weight: 600;
    font-size: 32px; line-height: 1.05;
  }
  .person-title {
    font-family: Roboto, sans-serif; font-size: 19px; margin-top: 2px; margin-bottom: 14px;
  }
  .contact-list { list-style: none; font-family: Roboto, sans-serif; font-size: 18.5px; }
  .contact-list li {
    display: flex; justify-content: flex-end; align-items: center;
    gap: 12px; height: 25.5px; white-space: nowrap;
  }
  .contact-list svg { width: 18px; height: 18px; fill: var(--white); flex: none; }

  .back-brand {
    left: 0; right: 0; top: 190px; justify-content: center;
    font-size: 62px; color: var(--white);
  }
  .back-brand .brand-mark { width: 28px; height: 28px; background: var(--white); }
  .back-site {
    position: absolute; left: 0; right: 0; top: 390px;
    text-align: center; color: var(--white);
    font-family: Roboto, sans-serif; font-size: 19px; letter-spacing: 3.2px;
  }
</style>
</head>
<body>

<section class="card card-front">
  <svg class="front-wave" viewBox="0 0 800 457" aria-hidden="true">
    <path d="M0 385 C170 280 330 195 560 200 C680 203 760 230 800 255 L800 262 C740 232 660 212 560 212 C360 212 190 300 0 396 Z" fill="var(--grey)"/>
    <path d="M0 398 C190 300 360 214 560 214 C665 214 745 236 800 262 L800 457 L0 457 Z" fill="var(--brand-blue)"/>
  </svg>

  <div class="brand front-brand"><span class="brand-mark"></span>Verdant Systems</div>

  <div class="contact-block">
    <p class="person-name">Calvin Borsted</p>
    <p class="person-title">Owner</p>
    <ul class="contact-list">
      <li>555-214-0186
        <svg viewBox="0 0 24 24"><path d="M6.6 10.8c1.4 2.8 3.8 5.1 6.6 6.6l2.2-2.2c.3-.3.7-.4 1-.2 1.1.4 2.3.6 3.6.6.6 0 1 .4 1 1V20c0 .6-.4 1-1 1C10.6 21 3 13.4 3 4c0-.6.4-1 1-1h3.5c.6 0 1 .4 1 1 0 1.3.2 2.5.6 3.6.1.3 0 .7-.2 1l-2.3 2.2z"/></svg>
      </li>
      <li>555-307-4421
        <svg viewBox="0 0 24 24"><path d="M7 1h10a2 2 0 0 1 2 2v18a2 2 0 0 1-2 2H7a2 2 0 0 1-2-2V3a2 2 0 0 1 2-2zm0 3v14h10V4H7zm5 15.5a1 1 0 1 0 0 2 1 1 0 0 0 0-2z"/></svg>
      </li>
      <li>info@verdantsystems.com
        <svg viewBox="0 0 24 24"><path d="M2 5h20v2l-10 6L2 7V5zm0 4.3l10 6 10-6V19H2V9.3z"/></svg>
      </li>
      <li>www.verdantsystems.com
        <svg viewBox="0 0 24 24"><path d="M12 2a10 10 0 1 0 0 20 10 10 0 0 0 0-20zm-1 17.9A8 8 0 0 1 4.2 10L9 14.8v1a2 2 0 0 0 2 2v2.1zm6.9-2.5a2 2 0 0 0-1.9-1.4h-1v-3a1 1 0 0 0-1-1H8v-2h2a1 1 0 0 0 1-1V7h2a2 2 0 0 0 2-2v-.4a8 8 0 0 1 2.9 12.8z"/></svg>
      </li>
      <li>1420 Harlow St, Suite 300, Springfield, IL 62704
        <svg viewBox="0 0 24 24"><path d="M12 2a7 7 0 0 0-7 7c0 5.2 7 13 7 13s7-7.8 7-13a7 7 0 0 0-7-7zm0 9.5a2.5 2.5 0 1 1 0-5 2.5 2.5 0 0 1 0 5z"/></svg>
      </li>
    </ul>
  </div>
</section>

<section class="card card-back">
  <div class="brand back-brand"><span class="brand-mark"></span>Verdant Systems</div>
  <p class="back-site">www.verdantsystems.com</p>
</section>

</body>
</html>
```